Accountability Project Graphics

I want to create 10 social media graphics (new Instagram size 4:5 (1080 x 1350 pixels) focusing on our Quilvo Accountability App, using any of the 3 pictures attached. Use the attached pics only, NO RANDOM STOCK PHOTOGRAPHY. For the color scheme, use the landing page colors/fonts (attached).
You can add any of the 3 photos attached but I mainly need BOLD text that includes these headlines and sub-headlines on them.
Please NOTE for all the headlines below, also add this sub-headline on each graphic:
Stay Consistent with RT in Your Pocket!
Here are the headlines:
• Stop Starting Over Every Monday
• You don't need more willpower. You need more support
• Built for women who are tired of doing this alone
• When Motivation Fades, RT Checks In
• The Support System You've Been Missing
• Support When Motivation Disappears
• What if RT Checked in Every Day?
• The Missing Piece Isn't Another Diet
• Eat the food you love. Stay accountable every day.
• One Bad Meal Doesn't Mean You Failed
women over 40 trying to lose weight

```html
<!DOCTYPE html>
<html lang="en">
<head>
<meta charset="utf-8">
<title>Quilvo Accountability – Social Graphics</title>
<link href="https://fonts.googleapis.com/css2?family=Bebas+Neue&family=Abril+Fatface&family=Libre+Baskerville:ital@0;1&family=Barlow+Semi+Condensed:wght@600;700&display=swap" rel="stylesheet">
<style>
:root{
  --board:#333335;
  --pink:#d64f86;
  --plum:#2d1938;
  --blush-top:#fcebf2;
  --blush-bottom:#f3c4d7;
  --white:#ffffff;
  --photo-skin:#7a4b3a;
  --photo-dark:#231a24;
  --photo-warm:#e9c9b6;
}
*{margin:0;padding:0;box-sizing:border-box}
html,body{width:1200px;height:616px;overflow:hidden;background:var(--board)}
.board{position:relative;width:1200px;height:616px;background:var(--board)}
.tile{position:absolute;width:214px;height:267px;overflow:hidden;background:linear-gradient(180deg,var(--blush-top),var(--blush-bottom))}
.row-1{top:32px}.row-2{top:314px}
.col-1{left:36px}.col-2{left:266px}.col-3{left:497px}.col-4{left:723px}.col-5{left:952px}
.photo{position:absolute}
.photo--portrait{background:linear-gradient(180deg,var(--photo-skin) 0%,var(--photo-dark) 35%,var(--photo-dark) 100%)}
.photo--hug{background:linear-gradient(135deg,#3a2a4a 0%,var(--photo-skin) 40%,#e0528f 70%,#f2d7e3 100%)}
.photo--duo{background:linear-gradient(180deg,var(--photo-warm) 0%,#4a3a3a 45%,#3b4c6e 100%)}
.fade-bottom::after{content:"";position:absolute;left:0;right:0;bottom:0;height:40%;background:linear-gradient(180deg,transparent,var(--blush-bottom))}
.fade-top::after{content:"";position:absolute;left:0;right:0;top:0;height:30%;background:linear-gradient(0deg,transparent,var(--blush-top))}
.type{position:absolute;left:0;top:0;width:214px;height:267px;overflow:visible}
.cond{font-family:"Bebas Neue",sans-serif}
.serif{font-family:"Abril Fatface",serif}
.ital{font-family:"Libre Baskerville",serif;font-style:italic}
.pink{fill:var(--pink)}.plum{fill:var(--plum)}.white{fill:var(--white)}
.rule{stroke:var(--plum);stroke-width:.8;opacity:.6}
.dash{stroke:var(--pink);stroke-width:1}
.pill{position:absolute;background:var(--white);border-radius:12px;font-family:"Barlow Semi Condensed",sans-serif;font-weight:700;font-size:8.5px;color:var(--plum);white-space:nowrap;text-align:center}
.pill em{font-style:normal;color:var(--pink)}
.pill--stack{text-align:left;line-height:1.25}
.sub{position:absolute;font-family:"Barlow Semi Condensed",sans-serif;font-weight:700;font-size:10px;line-height:1.3;color:var(--plum)}
.sub em{font-style:normal;color:var(--pink)}
.stop-band{position:absolute;left:0;top:19px;width:155px;height:44px;background:var(--pink)}
.tag-box{position:absolute;background:var(--plum);color:var(--white);font-family:"Bebas Neue",sans-serif;font-size:10px;line-height:1.25;padding:10px 0 0 5px}
</style>
</head>
<body>
<main class="board">

  <!-- 1 Stop starting over -->
  <section class="tile row-1 col-1">
    <div class="photo photo--portrait" role="img" aria-label="Smiling coach in a black lace top, standing with hand on hip" style="left:132px;top:0;width:82px;height:267px"></div>
    <div class="stop-band"></div>
    <svg class="type" viewBox="0 0 214 267">
      <text class="serif white" x="14" y="56" font-size="46" textLength="112" lengthAdjust="spacingAndGlyphs">STOP</text>
      <text class="cond plum" x="14" y="104" font-size="43" textLength="117" lengthAdjust="spacingAndGlyphs">STARTING</text>
      <text class="serif plum" font-size="21" textLength="68" lengthAdjust="spacingAndGlyphs" transform="translate(31,178) rotate(-90)">OVER</text>
      <line class="rule" x1="35" y1="110" x2="35" y2="186"/>
      <text class="cond pink" x="38" y="148" font-size="50" textLength="92" lengthAdjust="spacingAndGlyphs">EVERY</text>
      <text class="cond pink" x="38" y="181" font-size="40" textLength="91" lengthAdjust="spacingAndGlyphs">MONDAY</text>
      <line class="rule" x1="35" y1="186" x2="129" y2="186"/>
    </svg>
    <div class="sub" style="left:14px;top:191px">Stay Consistent with<br><em>RT in Your Pocket!</em></div>
  </section>

  <!-- 2 Willpower vs support -->
  <section class="tile row-1 col-2">
    <div class="photo photo--hug fade-bottom" role="img" aria-label="Coach hugging a laughing client in a store" style="left:0;top:0;width:214px;height:135px"></div>
    <svg class="type" viewBox="0 0 214 267">
      <line class="dash" x1="20" y1="150" x2="35" y2="150"/>
      <text class="ital plum" x="107" y="154" font-size="12" text-anchor="middle">You don't need more</text>
      <line class="dash" x1="179" y1="150" x2="194" y2="150"/>
      <text class="cond pink" x="20" y="194" font-size="50" textLength="174" lengthAdjust="spacingAndGlyphs">WILLPOWER</text>
      <text class="cond plum" x="20" y="221" font-size="30" textLength="38" lengthAdjust="spacingAndGlyphs">YOU</text>
      <text class="cond plum" x="20" y="239" font-size="24" textLength="38" lengthAdjust="spacingAndGlyphs">NEED</text>
      <text class="cond plum" font-size="24" textLength="40" lengthAdjust="spacingAndGlyphs" transform="translate(82,239) rotate(-90)">MORE</text>
      <line class="rule" x1="87" y1="199" x2="87" y2="239"/>
      <text class="cond pink" x="92" y="238" font-size="55" textLength="102" lengthAdjust="spacingAndGlyphs">SUPPORT</text>
    </svg>
    <div class="pill" style="left:19px;top:243px;width:177px;height:16px;line-height:16px">Stay Consistent with <em>RT in Your Pocket!</em></div>
  </section>

  <!-- 3 Built for women -->
  <section class="tile row-1 col-3">
    <div class="photo photo--duo fade-top" role="img" aria-label="Coach and client laughing together, arm in arm" style="left:0;top:152px;width:214px;height:115px"></div>
    <div class="tag-box" style="left:29px;top:95px;width:65px;height:40px">WHO ARE TIRED<br>OF DOING THIS</div>
    <svg class="type" viewBox="0 0 214 267">
      <text class="serif plum" x="29" y="36" font-size="30" textLength="157" lengthAdjust="spacingAndGlyphs">BUILT FOR</text>
      <text class="cond pink" x="30" y="90" font-size="71" textLength="156" lengthAdjust="spacingAndGlyphs">WOMEN</text>
      <line class="rule" x1="94" y1="95" x2="186" y2="95"/>
      <text class="cond pink" x="100" y="132" font-size="47" textLength="85" lengthAdjust="spacingAndGlyphs">ALONE</text>
      <line class="rule" x1="94" y1="135" x2="186" y2="135"/>
    </svg>
    <div class="pill" style="left:20px;top:141px;width:175px;height:16px;line-height:16px">Stay Consistent with <em>RT in Your Pocket!</em></div>
  </section>

  <!-- 4 When motivation fades -->
  <section class="tile row-1 col-4">
    <div class="photo photo--portrait" role="img" aria-label="Smiling coach in a black lace top, hand on hip" style="left:144px;top:0;width:70px;height:267px"></div>
    <svg class="type" viewBox="0 0 214 267">
      <line class="dash" x1="17" y1="28" x2="40" y2="28"/>
      <text class="cond plum" x="79" y="41" font-size="37" text-anchor="middle" textLength="66" lengthAdjust="spacingAndGlyphs">WHEN</text>
      <line class="dash" x1="118" y1="28" x2="141" y2="28"/>
      <text class="cond pink" x="8" y="87" font-size="60" textLength="134" lengthAdjust="spacingAndGlyphs">MOTIVATION</text>
      <text class="cond plum" x="8" y="144" font-size="70" textLength="133" lengthAdjust="spacingAndGlyphs">FADES</text>
      <text class="serif pink" x="9" y="214" font-size="85" textLength="99" lengthAdjust="spacingAndGlyphs">RT</text>
      <line class="rule" x1="111" y1="155" x2="111" y2="215" style="stroke:var(--pink)"/>
      <text class="ital pink" font-size="12" textLength="60" lengthAdjust="spacingAndGlyphs" transform="translate(116,155) rotate(90)">Checks In</text>
    </svg>
    <div class="pill pill--stack" style="left:10px;top:227px;width:152px;height:30px;border-radius:15px;padding:5px 0 0 16px;font-size:9px">Stay Consistent with<br><em>RT in Your Pocket!</em></div>
  </section>

  <!-- 5 Support system -->
  <section class="tile row-1 col-5">
    <div class="photo photo--hug fade-bottom" role="img" aria-label="Coach hugging a laughing client in a store" style="left:0;top:0;width:214px;height:170px"></div>
    <svg class="type" viewBox="0 0 214 267">
      <line class="dash" x1="18" y1="160" x2="33" y2="160"/>
      <text class="ital plum" x="107" y="164" font-size="13" text-anchor="middle">The Support System</text>
      <line class="dash" x1="181" y1="160" x2="196" y2="160"/>
      <text class="cond plum" x="16" y="197" font-size="29" textLength="62" lengthAdjust="spacingAndGlyphs">YOU'VE</text>
      <text class="cond plum" x="16" y="232" font-size="40" textLength="62" lengthAdjust="spacingAndGlyphs">BEEN</text>
      <line class="rule" x1="83" y1="176" x2="83" y2="232"/>
      <text class="cond pink" x="89" y="229" font-size="77" textLength="110" lengthAdjust="spacingAndGlyphs">MISSING</text>
    </svg>
    <div class="pill" style="left:19px;top:240px;width:176px;height:16px;line-height:16px">Stay Consistent with <em>RT in Your Pocket!</em></div>
  </section>

  <!-- 6 Support when motivation disappears -->
  <section class="tile row-2 col-1">
    <div class="photo photo--duo fade-bottom" role="img" aria-label="Coach and client laughing together, arm in arm" style="left:0;top:0;width:214px;height:140px"></div>
    <svg class="type" viewBox="0 0 214 267">
      <text class="cond plum" x="19" y="162" font-size="40" textLength="177" lengthAdjust="spacingAndGlyphs">SUPPORT WHEN</text>
      <line class="rule" x1="19" y1="165" x2="196" y2="165"/>
      <text class="serif pink" x="19" y="192" font-size="29" textLength="177" lengthAdjust="spacingAndGlyphs">MOTIVATION</text>
      <text class="cond plum" x="19" y="230" font-size="48" textLength="177" lengthAdjust="spacingAndGlyphs">DISAPPEARS</text>
    </svg>
    <div class="pill" style="left:19px;top:240px;width:177px;height:16px;line-height:16px">Stay Consistent with <em>RT in Your Pocket!</em></div>
  </section>

  <!-- 7 What if RT checked in -->
  <section class="tile row-2 col-2">
    <div class="photo photo--portrait" role="img" aria-label="Smiling coach portrait in a black top" style="left:125px;top:147px;width:89px;height:120px"></div>
    <svg class="type" viewBox="0 0 214 267">
      <text class="cond plum" x="20" y="55" font-size="55" textLength="175" lengthAdjust="spacingAndGlyphs">WHAT IF <tspan class="pink">RT</tspan></text>
      <text class="cond pink" x="20" y="106" font-size="60" textLength="175" lengthAdjust="spacingAndGlyphs">CHECKED</text>
      <text class="serif plum" x="18" y="141" font-size="40" textLength="180" lengthAdjust="spacingAndGlyphs">IN EVERY</text>
      <text class="serif plum" x="18" y="177" font-size="38" textLength="96" lengthAdjust="spacingAndGlyphs">DAY?</text>
    </svg>
    <div class="pill pill--stack" style="left:14px;top:186px;width:126px;height:65px;border-radius:32px;padding:10px 0 0 18px;font-size:12.5px">Stay Consistent<br>with <em>RT in Your</em><br><em>Pocket!</em></div>
  </section>

  <!-- 8 Missing piece -->
  <section class="tile row-2 col-3">
    <div class="photo photo--hug fade-top" role="img" aria-label="Coach hugging a laughing client in a store" style="left:0;top:136px;width:214px;height:131px"></div>
    <svg class="type" viewBox="0 0 214 267">
      <text class="serif plum" x="21" y="34" font-size="27" textLength="172" lengthAdjust="spacingAndGlyphs">THE MISSING</text>
      <text class="cond plum" x="24" y="77" font-size="50" textLength="168" lengthAdjust="spacingAndGlyphs">PIECE ISN'T</text>
      <line class="rule" x1="24" y1="84" x2="192" y2="84"/>
      <text class="cond pink" x="22" y="118" font-size="39" textLength="170" lengthAdjust="spacingAndGlyphs">ANOTHER DIET</text>
    </svg>
    <div class="pill" style="left:22px;top:126px;width:170px;height:18px;line-height:18px">Stay Consistent with <em>RT in Your Pocket!</em></div>
  </section>

  <!-- 9 Eat the food you love -->
  <section class="tile row-2 col-4">
    <div class="photo photo--duo fade-bottom" role="img" aria-label="Coach and client laughing together, arm in arm" style="left:0;top:0;width:214px;height:150px"></div>
    <svg class="type" viewBox="0 0 214 267">
      <text class="serif plum" x="21" y="157" font-size="23" textLength="170" lengthAdjust="spacingAndGlyphs">EAT THE FOOD</text>
      <text class="cond pink" font-size="26" textLength="65" lengthAdjust="spacingAndGlyphs" transform="translate(41,230) rotate(-90)">YOU LOVE</text>
      <text class="cond pink" x="48" y="183" font-size="25" textLength="143" lengthAdjust="spacingAndGlyphs">STAY ACCOUNTABLE</text>
      <text class="cond plum" x="48" y="228" font-size="57" textLength="143" lengthAdjust="spacingAndGlyphs">EVERY DAY</text>
    </svg>
    <div class="pill" style="left:22px;top:237px;width:170px;height:17px;line-height:17px">Stay Consistent with <em>RT in Your Pocket!</em></div>
  </section>

  <!-- 10 One bad meal -->
  <section class="tile row-2 col-5">
    <div class="photo photo--portrait" role="img" aria-label="Smiling coach in a black lace top, hand on hip" style="left:0;top:0;width:91px;height:267px"></div>
    <svg class="type" viewBox="0 0 214 267">
      <text class="serif pink" x="98" y="47" font-size="43" textLength="99" lengthAdjust="spacingAndGlyphs">ONE</text>
      <text class="serif pink" x="98" y="84" font-size="43" textLength="99" lengthAdjust="spacingAndGlyphs">BAD</text>
      <text class="serif pink" x="98" y="114" font-size="33" textLength="100" lengthAdjust="spacingAndGlyphs">MEAL</text>
      <line class="rule" x1="98" y1="122" x2="198" y2="122"/>
      <text class="cond plum" x="98" y="156" font-size="37" textLength="99" lengthAdjust="spacingAndGlyphs">DOESN'T</text>
      <text class="cond plum" x="98" y="204" font-size="56" textLength="99" lengthAdjust="spacingAndGlyphs">MEAN</text>
      <text class="cond plum" x="98" y="228" font-size="23" textLength="99" lengthAdjust="spacingAndGlyphs">YOU FAILED</text>
    </svg>
    <div class="pill" style="left:22px;top:237px;width:171px;height:18px;line-height:18px">Stay Consistent with <em>RT in Your Pocket!</em></div>
  </section>

</main>
</body>
</html>
```